Web Design Project for Communications Agency

The design I need (PSD file) is for an agency offering specialised PR and communications services for customers in the healthcare sector.

OBJECTIVES OF THE WEBSITE:
1. To promote the agency's communication services
2. To position Solène Brivard as an industry leader, an expert in healthcare PR and communications by highlighting blogposts and social media.

WHAT I NEED:
1st, I need the design for the Home Page ONLY.
Once approved, I will need the other pages designed as well. (Here is prototype that we've already developed for the Website that will guide you in the design:
http://qorvelle.net/solenebrivard/)

VISUAL INSPIRATION
We want to give this Website a "Flat Design" look. Here are some websites for inspiration :
- http://tavrolinkworks.com/#!/process
- http://www.brindlemoss.co/
- http://quellaroft.com/

Also, reuse images found on the company's current Website :
http://www.solenebrivard.com/fr/index.html

HOMEPAGE MAIN ELEMENTS:
1. Main menu : 6 sections
Accueil | Agence | Services | Approche | Publications | Contact

2. Main Call To Action (big dark rectangle in prototype):
Can be slider or just an information bloc.

3. Publications récentes :
The 4 latest blog posts must be features on the homepage (will be linked with the "Publications" section)

4. Dynamic Footer :
Contains a Chirpline feed and a Subscribe to our Newsletter feature (revecez nos publications)

OTHER PAGES (to design once Homepage is approved)
- Agence (about us)
- Services (our team)
- Approche (our approach)
- Publications (blog articles)
- Contact (Contact us)

Industry/Entity Type

Communications

Requirements
Must have
• Please refer to prototype :
http://qorvelle.net/solenebrivard/
Must have ALL features present in prototype.

Also, must reuse this picture in the design : http://solenebrivard.com/static/images/home-big-box.jpg

Finally, you will find attached the company logo.

```html
<!DOCTYPE html>
<html lang="fr">
<head>
<meta charset="utf-8">
<title>Solène Brivard — Accueil</title>
<link href="https://fonts.googleapis.com/css2?family=Open+Sans:ital,wght@0,300;0,400;0,600;0,700;1,400&display=swap" rel="stylesheet">
<style>
:root{
  --red:#e23c45;
  --red-dark:#c7272f;
  --ink:#333;
  --muted:#666;
  --paper:#f7f7f7;
  --body:#eeeeee;
  --band:#4a4a4c;
  --black:#000;
  --base:#1e1e1e;
  --link:#3fb6e0;
}
*{box-sizing:border-box;margin:0;padding:0}
html,body{width:686px;height:1200px;overflow:hidden}
body{font-family:"Open Sans",Arial,sans-serif;color:var(--ink);background:var(--paper);position:relative}
.abs{position:absolute}

/* header */
.site-header{position:absolute;left:0;top:0;width:686px;height:81px;background:var(--paper);border-bottom:2px solid var(--red)}
.brand{position:absolute;left:70px;top:8px;width:110px}
.brand-name{font-size:19px;line-height:19px;color:var(--red);font-weight:400;letter-spacing:-.5px}
.brand-tag{margin-top:8px;font-size:6px;line-height:7px;font-weight:700;color:#555;border-top:1px solid var(--red);padding-top:3px;width:62px}
.social-top{position:absolute;left:423px;top:24px;display:flex;gap:4px}
.social-top span{width:16px;height:16px;display:block}
.search{position:absolute;left:503px;top:22px;width:108px;height:16px;border:1px solid #ccc;border-radius:3px;background:#fff;font-size:8px;color:#aaa;padding:2px 6px}
.search svg{position:absolute;right:4px;top:3px}
.main-nav{position:absolute;left:297px;top:61px;display:flex;font-size:8.5px;color:#333}
.main-nav a{color:inherit;text-decoration:none;padding:4px 8px;height:18px;margin-right:5px}
.main-nav a.active{background:var(--red);color:#fff;border-radius:3px 3px 0 0}

/* hero */
.hero-photo{position:absolute;left:0;top:81px;width:686px;height:215px;background:linear-gradient(90deg,#dfe6ea,#f2f4f5 30%,#e8ebec 55%,#f4f2ef 75%,#dcdfe2)}
.cta-band{position:absolute;left:0;top:296px;width:686px;height:77px;background:var(--band);border-bottom:3px solid var(--red)}
.cta-text{position:absolute;left:71px;top:14px;font-size:15.5px;line-height:20px;font-weight:300;color:#fff}
.cta-btn{position:absolute;left:459px;top:23px;width:154px;height:28px;background:var(--red);border-radius:3px;color:#fff;font-size:15px;font-weight:600;text-align:center;line-height:28px}

/* publications */
.publications{position:absolute;left:0;top:373px;width:686px;height:621px;background:var(--body)}
.section-title{position:absolute;left:68px;top:17px;font-size:22px;font-weight:300;color:#333}
.pub-card{position:absolute;left:63px;width:566px;height:162px;background:var(--red);border-radius:4px}
.pub-title{position:absolute;left:8px;top:10px;font-size:12.5px;color:#fff}
.pub-date{position:absolute;left:8px;top:27px;font-size:8.5px;font-style:italic;color:#222}
.pub-excerpt{position:absolute;left:8px;top:48px;width:300px;font-size:6.4px;line-height:14.8px;color:#fff}
.read-more{position:absolute;left:-6px;top:130px;width:88px;height:18px;background:var(--red-dark);border-radius:2px;color:#fff;font-size:8.5px;font-weight:600;line-height:18px;padding-left:16px}
.read-more svg{position:absolute;left:-3px;top:-2px}
.pub-photo{position:absolute;left:316px;top:5px;width:244px;height:151px;border:1px solid #fff}

/* footer */
.site-footer{position:absolute;left:0;top:994px;width:686px;height:168px;background:var(--black)}
.feed-name{position:absolute;left:70px;top:12px;font-size:26px;font-weight:700;color:#fff;letter-spacing:-.5px;display:flex;align-items:center;gap:8px}
.feed-name i{width:12px;height:12px;background:var(--link);border-radius:50%;display:block}
.tweets{position:absolute;left:70px;top:64px;width:300px;font-size:7.6px;line-height:13px;color:#aaa}
.tweets p{margin-bottom:9.5px}
.tweets b{color:var(--link);font-weight:400}
.newsletter{position:absolute;left:395px;top:12px;width:220px;color:#fff}
.newsletter h2{font-size:16.5px;font-weight:400;margin-bottom:14px}
.newsletter label{display:block;font-size:9.5px;line-height:12px}
.newsletter .field{width:218px;height:15px;background:#fff;border:1px solid #999;margin:2px 0 7px}
.subscribe{display:inline-block;margin-top:5px;background:var(--red);border-radius:3px;padding:3px 6px;font-size:9.5px;color:#fff}
.base-bar{position:absolute;left:0;top:1162px;width:686px;height:38px;background:var(--base)}
.copyright{position:absolute;left:70px;top:14px;font-size:7.5px;color:#ccc}
.social-bottom{position:absolute;left:482px;top:14px;display:flex;gap:11px}
.social-bottom span{width:9px;height:9px;border-radius:50%;background:#ddd;display:block}
</style>
</head>
<body>

<header class="site-header">
  <div class="brand">
    <div class="brand-name">Solène<br>Brivard</div>
    <div class="brand-tag">GESTION D'ENJEUX<br>AFFAIRES PUBLIQUES</div>
  </div>
  <div class="social-top" aria-label="Réseaux sociaux">
    <span style="background:#2a5aa8"></span>
    <span style="background:#f08a1c"></span>
    <span style="background:#1e74b0"></span>
    <span style="background:#555"></span>
  </div>
  <div class="search">Search Text Here
    <svg width="9" height="9" viewBox="0 0 9 9"><circle cx="3.5" cy="3.5" r="2.6" fill="none" stroke="#999" stroke-width="1"/><line x1="5.5" y1="5.5" x2="8.5" y2="8.5" stroke="#999" stroke-width="1.2"/></svg>
  </div>
  <nav class="main-nav">
    <a class="active">Accueil</a><a>Agence</a><a>Services</a><a>Approche</a><a>Publications</a><a>Contact</a>
  </nav>
</header>

<div class="hero-photo" role="img" aria-label="Photo d'une équipe médicale en blouses blanches réunie autour de documents"></div>

<section class="cta-band">
  <p class="cta-text">Cabinet-conseil en communications et affaires publiques<br>spécialisé dans le secteur de la santé.</p>
  <div class="cta-btn">En savior plus</div>
</section>

<main class="publications">
  <h1 class="section-title">Publication récentes</h1>

  <article class="pub-card" style="top:63px">
    <h3 class="pub-title">Titre de la publication</h3>
    <p class="pub-date">23 juillet 2013</p>
    <p class="pub-excerpt">Lorem ipsum dolor sit amet, consectetur adipisicing elit, sed do eiusmod tempor incididunt ut labore et dolore magna aliqua. Ut enim ad minim veniam, quis nostrud exercitation ullamco laboris nisi ut aliquip ex ea commodo consequat. Duis aute irure dolor in reprehenderit in voluptate velit esse cillum dolore eu fugiat nulla pariatur. Excepteur sint occaecat cupidatat non proident, sunt in culpa qui officia deserunt. mollit anim id est laborum.</p>
    <div class="read-more"><svg width="20" height="22" viewBox="0 0 20 22"><circle cx="10" cy="11" r="9" fill="#fff"/><circle cx="10" cy="11" r="7" fill="var(--red)"/><path d="M8 7l4 4-4 4" fill="none" stroke="#fff" stroke-width="2"/></svg>Read More</div>
    <div class="pub-photo" role="img" aria-label="Photo d'une salle d'imagerie médicale avec table d'examen" style="background:linear-gradient(135deg,#cfd5d8,#eef0f0 50%,#b9c0c4)"></div>
  </article>

  <article class="pub-card" style="top:249px">
    <h3 class="pub-title">Titre de la publication</h3>
    <p class="pub-date">23 juillet 2013</p>
    <p class="pub-excerpt">Lorem ipsum dolor sit amet, consectetur adipisicing elit, sed do eiusmod tempor incididunt ut labore et dolore magna aliqua. Ut enim ad minim veniam, quis nostrud exercitation ullamco laboris nisi ut aliquip ex ea commodo consequat. Duis aute irure dolor in reprehenderit in voluptate velit esse cillum dolore eu fugiat nulla pariatur. Excepteur sint occaecat cupidatat non proident, sunt in culpa qui officia deserunt. mollit anim id est laborum.</p>
    <div class="read-more"><svg width="20" height="22" viewBox="0 0 20 22"><circle cx="10" cy="11" r="9" fill="#fff"/><circle cx="10" cy="11" r="7" fill="var(--red)"/><path d="M8 7l4 4-4 4" fill="none" stroke="#fff" stroke-width="2"/></svg>Read More</div>
    <div class="pub-photo" role="img" aria-label="Photo d'instruments chirurgicaux sur un plateau métallique" style="background:linear-gradient(135deg,#3e4a5c,#a9b3c2 45%,#56637a)"></div>
  </article>

  <article class="pub-card" style="top:434px">
    <h3 class="pub-title">Titre de la publication</h3>
    <p class="pub-date">23 juillet 2013</p>
    <p class="pub-excerpt">Lorem ipsum dolor sit amet, consectetur adipisicing elit, sed do eiusmod tempor incididunt ut labore et dolore magna aliqua. Ut enim ad minim veniam, quis nostrud exercitation ullamco laboris nisi ut aliquip ex ea commodo consequat. Duis aute irure dolor in reprehenderit in voluptate velit esse cillum dolore eu fugiat nulla pariatur. Excepteur sint occaecat cupidatat non proident, sunt in culpa qui officia deserunt. mollit anim id est laborum.</p>
    <div class="read-more"><svg width="20" height="22" viewBox="0 0 20 22"><circle cx="10" cy="11" r="9" fill="#fff"/><circle cx="10" cy="11" r="7" fill="var(--red)"/><path d="M8 7l4 4-4 4" fill="none" stroke="#fff" stroke-width="2"/></svg>Read More</div>
    <div class="pub-photo" role="img" aria-label="Photo de chirurgiens en salle d'opération" style="background:linear-gradient(135deg,#1aa8b8,#8fd6df 50%,#2b8b9e)"></div>
  </article>
</main>

<footer class="site-footer">
  <div class="feed-name">Chirpline<i></i></div>
  <div class="tweets">
    <p>Velit esse cillum dolore eu fugiat nulla pariatur. Excepteur sint occaecat cupidatat non proident. <b>@SoleneBrivard #EnjeuSanté</b></p>
    <p>Velit esse eu fugiat nulla pariatur. Excepteur sint occaecat cupidatat non proident. <b>@SoleneBrivard #EnjeuSanté</b></p>
    <p>Velit esse cillum dolore eu fugiat nulla pariatur. Excepteur sint occaecat cupidatat non proident. <b>@SoleneBrivard #EnjeuSanté</b></p>
  </div>
  <form class="newsletter">
    <h2>Recevez nos publications</h2>
    <label>Votre nom</label>
    <div class="field"></div>
    <label>Votre courriel</label>
    <div class="field"></div>
    <span class="subscribe">Abbonnez-vous</span>
  </form>
</footer>

<div class="base-bar">
  <p class="copyright">© Copyrights 2013 All rights Reserved</p>
  <div class="social-bottom" aria-label="Réseaux sociaux">
    <span></span><span></span><span></span><span></span><span></span><span></span><span></span>
  </div>
</div>

</body>
</html>
```